Design and Renovation Company Luxury Business Card

I want to create a luxury business card for a Design and Renovation Firm . We will use our current logo. The company name is 528BUILDA. We do not want anything standard. We need a very unique concept.
Please see uploaded inspiration. I really like the textured paper option. I would like the card to be thick with debossing, and/or embossing options. The logo has orange in it but I would like to see the card with and without the orange. I think the orange may make the company feel less high-end. The goal is to elevate the logo not match its vibe per se of the logo. We want something very unique, not standard at all!
I would like a space for :
Logo,
Name,
Position,
Email,
Office number,
Website Address,
Business Address,
Thank you!
Have fun!
Target Market(s)
Home owners Age 35 +
Industry/Entity Type
Design and Renovation
Contact Information for Business Card
Logo, Name, Position, Email, Office number, Website Address, Business Address,.
Colors
Designer to choose colors to be used in the design.
Requirements
Must have
- A luxury designer feel. Must be black or dark grey but open to other luxury ideas.
Nice to have
- Gold, silver, black embossing or debossing. Textured paper design.
Should not have
- A cheap look and feel.

```html
<!DOCTYPE html>
<html lang="en">
<head>
<meta charset="utf-8">
<title>528BUILDA Business Card</title>
<link href="https://fonts.googleapis.com/css2?family=Poppins:wght@300;400;500&display=swap" rel="stylesheet">
<style>
  :root {
    --backdrop: #c8c8c8;
    --card: #000000;
    --ink: #ffffff;
    --ink-soft: #d9d9d9;
    --rule: #6b6b6b;
  }
  * { margin: 0; padding: 0; box-sizing: border-box; }
  html, body {
    width: 1136px;
    height: 1200px;
    overflow: hidden;
    background: var(--backdrop);
    font-family: "Poppins", sans-serif;
    color: var(--ink);
  }
  .sheet {
    position: relative;
    width: 1136px;
    height: 1200px;
  }
  .card {
    position: absolute;
    left: 88px;
    width: 960px;
    height: 549px;
    background: var(--card);
  }
  .card--front { top: 36px; }
  .card--back { top: 615px; }

  /* Front */
  .front-name {
    position: absolute;
    left: 480px;
    top: 275px;
    transform: translate(-50%, -50%);
    font-weight: 400;
    font-size: 56px;
    letter-spacing: 0;
    line-height: 1;
    color: var(--ink);
    white-space: nowrap;
  }

  /* Back */
  .spine {
    position: absolute;
    left: 54px;
    top: 80px;
    width: 1px;
    height: 400px;
    background: var(--rule);
  }
  .bullet {
    position: absolute;
    left: 54px;
    width: 16px;
    height: 16px;
    transform: translate(-50%, -50%);
  }
  .identity {
    position: absolute;
    left: 82px;
    top: 54px;
  }
  .identity__name {
    font-weight: 400;
    font-size: 36px;
    letter-spacing: 0;
    line-height: 1;
  }
  .identity__tagline {
    margin-top: 8px;
    font-size: 13px;
    font-weight: 400;
    letter-spacing: 0.3px;
    text-transform: uppercase;
  }
  .identity__role {
    margin-top: 4px;
    font-size: 20px;
    font-weight: 300;
    color: var(--ink-soft);
  }
  .contact {
    position: absolute;
    left: 82px;
    font-size: 20px;
    font-weight: 300;
    line-height: 1;
    color: var(--ink-soft);
    transform: translateY(-50%);
    white-space: nowrap;
  }
  .back-name {
    position: absolute;
    right: 54px;
    top: 448px;
    font-weight: 400;
    font-size: 34px;
    letter-spacing: 0;
    line-height: 1;
    white-space: nowrap;
  }
  .back-tagline {
    position: absolute;
    right: 54px;
    top: 490px;
    font-size: 11px;
    letter-spacing: 0.6px;
    font-weight: 400;
    white-space: nowrap;
  }
</style>
</head>
<body>
<main class="sheet">

  <section class="card card--front" aria-label="Business card front">
    <div class="front-name">528BUILDA</div>
  </section>

  <section class="card card--back" aria-label="Business card back">
    <span class="spine"></span>

    <svg class="bullet" style="top:73px" viewBox="0 0 16 16" aria-hidden="true">
      <circle cx="8" cy="8" r="8" fill="#000"/>
      <circle cx="8" cy="8" r="7" fill="#fff"/>
      <circle cx="8" cy="6" r="2.2" fill="#000"/>
      <path d="M4 12.2c.8-2 2.2-3 4-3s3.2 1 4 3z" fill="#000"/>
    </svg>
    <div class="identity">
      <div class="identity__name">528BUILDA</div>
      <div class="identity__tagline">Design and Renovation Firm</div>
      <div class="identity__role">Ceo</div>
    </div>

    <svg class="bullet" style="top:280px" viewBox="0 0 16 16" aria-hidden="true">
      <circle cx="8" cy="8" r="8" fill="#000"/>
      <circle cx="8" cy="8" r="6.5" fill="#fff"/>
      <path d="M5.6 4.6l1.4 1.6-.8 1c.6 1.2 1.4 2 2.6 2.6l1-.8 1.6 1.4-.9 1.2c-2.8-.4-4.8-2.4-5.2-5.2z" fill="#000"/>
    </svg>
    <div class="contact" style="top:280px">+ 1234567890</div>

    <svg class="bullet" style="top:313px" viewBox="0 0 16 16" aria-hidden="true">
      <circle cx="8" cy="8" r="8" fill="#000"/>
      <circle cx="8" cy="8" r="6.5" fill="#fff"/>
      <path d="M8 3.8a2.6 2.6 0 0 1 2.6 2.6c0 1.9-2.6 5.2-2.6 5.2S5.4 8.3 5.4 6.4A2.6 2.6 0 0 1 8 3.8z" fill="#000"/>
      <circle cx="8" cy="6.4" r="1" fill="#fff"/>
    </svg>
    <div class="contact" style="top:313px">Dummy City, Dummy Country</div>

    <svg class="bullet" style="top:349px" viewBox="0 0 16 16" aria-hidden="true">
      <circle cx="8" cy="8" r="8" fill="#000"/>
      <circle cx="8" cy="8" r="6.5" fill="#fff"/>
      <rect x="4.5" y="5.5" width="7" height="5" fill="#000"/>
      <path d="M4.8 5.8L8 8.4l3.2-2.6" stroke="#fff" stroke-width="0.8" fill="none"/>
    </svg>
    <div class="contact" style="top:349px">info@528buildadesign.com</div>

    <svg class="bullet" style="top:478px" viewBox="0 0 16 16" aria-hidden="true">
      <circle cx="8" cy="8" r="8" fill="#000"/>
      <circle cx="8" cy="8" r="6.5" fill="#fff"/>
      <circle cx="8" cy="8" r="3.6" fill="none" stroke="#000" stroke-width="1"/>
      <path d="M4.4 8h7.2M8 4.4c-1.6 2.2-1.6 5 0 7.2M8 4.4c1.6 2.2 1.6 5 0 7.2" stroke="#000" stroke-width="0.8" fill="none"/>
    </svg>
    <div class="contact" style="top:478px">www.528buildadesign.com</div>

    <div class="back-name">528BUILDA</div>
    <div class="back-tagline">Design and Renovation Firm</div>
  </section>

</main>
</body>
</html>
```